Laser Tattoo Removal Business Cards

We are looking for a professional business card design for a laser tattoo removal business. Ideally looking for a black business card design. The name of the business is Brightline Tattoo Removal. We place our cards at local tattoo shops so we ideally are looking for something trendy/edgy to draw both male and female clientele in.

Target Market(s)

Male/Female ages 18-60

Contact Information for Business Card

black background ideally.. hoping to stay within greys, whites and black

Font styles to use
Serif
Sans Serif

Colors
121212
a9a9a9
5c5c5c
f5f5f5
ffffff
7f7f7f
606060
848484
9d9d9d

Requirements
Must have
• Employee Info:
• Melissa Thornbury
• Chief Executive Offer
• m: 919.537.2846
• w: 919.362.4178
• f: 919.685.3907
• mthornbury@brightlinetattooremoval.example
• Address:
• 4615 Oakmere Pkwy, Suite 210
• Raleigh, NC 27654
• Website:
• www.brightlinetattooremoval.example
Nice to have
• Myabe business name on back or logo on back and employee info on the front

```html
<!DOCTYPE html>
<html lang="en">
<head>
<meta charset="utf-8">
<title>Brightline Tattoo Removal — Business Card</title>
<link href="https://fonts.googleapis.com/css2?family=Roboto:wght@400&family=Roboto+Condensed:wght@400;500&display=swap" rel="stylesheet">
<style>
  :root {
    --ink: #121212;
    --paper: #f5f5f5;
    --white: #ffffff;
    --grey-dark: #5c5c5c;
    --grey-mid: #7f7f7f;
    --grey-soft: #9d9d9d;
    --grey-light: #a9a9a9;
    --backdrop: #e2e2e2;
  }
  * { margin: 0; padding: 0; box-sizing: border-box; }
  html, body { width: 1200px; height: 960px; overflow: hidden; }
  body { background: var(--backdrop); position: relative; font-family: "Roboto", sans-serif; }

  .card { position: absolute; left: 313px; width: 600px; }
  .card-front { top: 113px; height: 332px; background: var(--paper); }
  .card-back { top: 472px; height: 343px; background: var(--ink); }

  .wordmark {
    position: absolute;
    font-family: "Roboto Condensed", sans-serif;
    font-weight: 400;
    text-transform: uppercase;
    text-align: center;
    line-height: 1.15;
    letter-spacing: 3px;
  }
  .card-front .wordmark { left: 30px; width: 225px; top: 130px; font-size: 30px; color: var(--ink); }
  .card-back .wordmark { left: 150px; width: 300px; top: 100px; font-size: 40px; color: var(--white); }
  .wordmark .mark-square {
    display: block; margin: 12px auto 0; width: 12px; height: 12px;
    background: currentColor;
  }

  .divider { position: absolute; left: 280px; top: 82px; width: 1px; height: 190px; background: var(--grey-light); }

  .contact { position: absolute; left: 305px; top: 80px; color: var(--grey-dark); }
  .contact .name {
    font-family: "Roboto Condensed", sans-serif; font-weight: 500;
    font-size: 21px; color: var(--ink); text-transform: uppercase; line-height: 24px;
  }
  .contact .role { font-size: 15px; color: var(--grey-mid); line-height: 20px; }
  .contact address { font-style: normal; font-size: 14.5px; line-height: 18px; margin-top: 6px; color: var(--grey-dark); }
  .contact-list { list-style: none; margin-top: 9px; }
  .contact-list li { display: flex; align-items: center; height: 19.3px; font-size: 14px; color: var(--grey-dark); }
  .contact-list li.long { font-size: 12.5px; }
  .contact-list svg { width: 13px; height: 13px; margin-right: 10px; fill: var(--ink); flex: none; }

  .back-url {
    position: absolute; left: 0; width: 600px; top: 292px; text-align: center;
    color: var(--white); font-size: 14px; letter-spacing: 2.2px;
  }
</style>
</head>
<body>
  <section class="card card-front">
    <div class="wordmark">Brightline<br>Tattoo Removal<span class="mark-square"></span></div>
    <div class="divider"></div>
    <div class="contact">
      <div class="name">Melissa Thornbury</div>
      <div class="role">Chief Executive Offer</div>
      <address>4615 Oakmere Pkwy, Suite 210<br>Raleigh, NC 27654</address>
      <ul class="contact-list">
        <li><svg viewBox="0 0 16 16"><path d="M3 1l3 3-1.5 2c1 2 3 4 5 5L11.5 9.5l3 3L12 15C6 14 2 10 1 4z"/></svg>919.362.4178</li>
        <li><svg viewBox="0 0 16 16"><path d="M4 0h8v16H4zM5.5 2v10h5V2z"/></svg>919.537.2846</li>
        <li><svg viewBox="0 0 16 16"><path d="M4 1h8v4H4zM1 6h14v7h-3v2H4v-2H1zM5 11v3h6v-3z"/></svg>919.685.3907</li>
        <li class="long"><svg viewBox="0 0 16 16"><path d="M1 3h14v10H1zM2 4.5v.5l6 4 6-4v-.5z"/></svg>mthornbury@brightlinetattooremoval.example</li>
        <li><svg viewBox="0 0 16 16"><circle cx="8" cy="8" r="7"/><path d="M4 5h3v3H4zM9 9h3v3H9z" fill="#f5f5f5"/></svg>www.brightlinetattooremoval.example</li>
      </ul>
    </div>
  </section>

  <section class="card card-back">
    <div class="wordmark">Brightline<br>Tattoo Removal<span class="mark-square"></span></div>
    <div class="back-url">www.brightlinetattooremoval.example</div>
  </section>
</body>
</html>
```